Charity requires Presentation Folder

We require a print design for a not-for-profit organisation called Harbour Lantern Trust. We require a professional presentation/display folder that is consistent with our brand (find examples of our other print material attached) however, new images can be used.

The template required can be found at:
http://www.foldwellprint.com.au/index.php?option=com_content&view=article&id=21&Itemid=140

Style: (Folder B)

```html
<!DOCTYPE html>
<html lang="en">
<head>
<meta charset="utf-8">
<title>Harbour Lantern Trust — Presentation Folder</title>
<link rel="stylesheet" href="https://fonts.googleapis.com/css2?family=Fira+Sans:ital,wght@0,300;0,400;0,600;1,300&display=swap">
<style>
  :root {
    --orange: #f7992b;
    --charcoal: #5f6063;
    --white: #ffffff;
    --backdrop: #d6d6d6;
  }
  html, body {
    margin: 0;
    padding: 0;
    width: 1200px;
    height: 915px;
    overflow: hidden;
    background: var(--backdrop);
    font-family: "Fira Sans", Arial, sans-serif;
  }
  .folder {
    position: relative;
    width: 1200px;
    height: 915px;
  }
  .die-shape {
    position: absolute;
    inset: 0;
  }
  .back-panel-quotes {
    position: absolute;
    left: 137px;
    top: 140px;
    width: 310px;
    color: var(--white);
  }
  .quote {
    margin: 0 0 22px;
  }
  .quote-text {
    margin: 0;
    font-style: italic;
    font-weight: 300;
    font-size: 13.5px;
    line-height: 20px;
  }
  .quote-author {
    margin: 0;
    font-weight: 600;
    font-size: 13px;
    line-height: 18px;
    color: var(--charcoal);
  }
  .front-contact {
    position: absolute;
    left: 527px;
    top: 89px;
    width: 479px;
    text-align: center;
  }
  .front-web {
    margin: 0;
    font-size: 13.5px;
    letter-spacing: 1.6px;
    color: var(--orange);
    font-weight: 400;
  }
  .front-email {
    margin: 7px 0 0;
    font-size: 10px;
    color: var(--charcoal);
    display: flex;
    align-items: center;
    justify-content: center;
    gap: 7px;
  }
  .social-square {
    width: 11px;
    height: 11px;
    background: var(--orange);
    border-radius: 1px;
  }
  .brand-name {
    position: absolute;
    left: 527px;
    top: 420px;
    width: 479px;
    display: flex;
    align-items: center;
    justify-content: center;
    gap: 14px;
    font-size: 30px;
    font-weight: 600;
    color: var(--charcoal);
  }
  .brand-dot {
    width: 26px;
    height: 26px;
    border-radius: 50%;
    background: var(--orange);
  }
</style>
</head>
<body>
<div class="folder">
  <svg class="die-shape" width="1200" height="915" viewBox="0 0 1200 915" aria-hidden="true">
    <!-- inside back panel -->
    <rect x="47" y="38" width="480" height="696" fill="var(--orange)"/>
    <!-- front cover -->
    <rect x="527" y="38" width="479" height="696" fill="var(--white)"/>
    <!-- bottom pocket flap -->
    <path d="M527 734 H1006 L993 868 Q992 880 980 880 H584 Q572 880 569 868 Z" fill="var(--orange)"/>
    <!-- side glue flap with card slot -->
    <path d="M1006 270 L1125 370 V632 Q1108 628 1098 640 Q1128 652 1128 682 Q1126 722 1085 722 Q1060 720 1055 706 L1006 735 Z" fill="var(--charcoal)"/>
  </svg>

  <div class="back-panel-quotes">
    <div class="quote">
      <p class="quote-text">“The miners lost because they had only the constitution. The other side had bayonets. In the end, bayonets always win.”</p>
      <p class="quote-author">Ada Colliery</p>
    </div>
    <div class="quote">
      <p class="quote-text">“We were all miners in our family. My father was a miner. My mother is a miner. These are miner’s hands, but we were all artists, I suppose, really. But I was the first one who had the urge to express myself on paper rather than at the coalface.”</p>
      <p class="quote-author">Martin Holloway</p>
    </div>
    <div class="quote">
      <p class="quote-text">“Art is a kind of mining,” he said. “The artist a variety of prospector searching for the sparkling silver of meaning in the earth.”</p>
      <p class="quote-author">Elspeth Marlow</p>
    </div>
  </div>

  <div class="front-contact">
    <p class="front-web">www.harbourlantern.org.au</p>
    <p class="front-email"><span class="social-square"></span>info@harbourlantern.org.au</p>
  </div>

  <div class="brand-name"><span class="brand-dot"></span>Harbour Lantern Trust</div>
</div>
</body>
</html>
```